New letter head for Air Conditioning business

We need a new professional letter head design to suit our new re-branded air conditioning business. Our new logo is attached

```html
<!DOCTYPE html>
<html lang="en">
<head>
<meta charset="UTF-8">
<title>Norvale Letterhead</title>
<link href="https://fonts.googleapis.com/css2?family=Poppins:wght@400;500;600&display=swap" rel="stylesheet">
<style>
  :root {
    --backdrop: #dcdde3;
    --paper-edge: #ebe8e9;
    --paper-mid: #ffffff;
    --brand-green: #67c087;
    --brand-dark: #414143;
    --ink: #111111;
    --signature-tone: #d9d9dc;
  }
  * { margin: 0; padding: 0; box-sizing: border-box; }
  html, body {
    width: 1200px; height: 1200px; overflow: hidden;
    background: var(--backdrop);
    font-family: "Poppins", sans-serif;
    color: var(--ink);
  }
  .letterhead {
    position: absolute; left: 204px; top: 40px;
    width: 792px; height: 1120px;
    background: linear-gradient(to bottom, var(--paper-edge) 0%, var(--paper-mid) 50%, var(--paper-edge) 100%);
    box-shadow: 0 14px 30px rgba(0,0,0,0.15);
    overflow: hidden;
  }
  .bands { position: absolute; inset: 0; }
  .band-green { fill: var(--brand-green); }
  .band-dark { fill: var(--brand-dark); }

  .brand { position: absolute; left: 48px; top: 72px; display: flex; align-items: center; gap: 18px; }
  .brand-mark { width: 56px; height: 56px; border-radius: 50%; background: var(--brand-green); }
  .brand-name { font-size: 30px; font-weight: 500; letter-spacing: 3px; color: var(--brand-dark); line-height: 1; }
  .brand-tagline { font-size: 6.5px; font-weight: 600; letter-spacing: 1.2px; color: var(--brand-green); margin-top: 5px; }

  .recipient-name { position: absolute; left: 58px; top: 244px; font-size: 18px; font-weight: 600; }
  .letter-date { position: absolute; right: 50px; top: 244px; font-size: 18px; font-weight: 600; }
  .recipient-address { position: absolute; left: 58px; top: 280px; font-size: 18px; font-weight: 500; }

  .letter-body { position: absolute; left: 52px; top: 340px; width: 690px; }
  .letter-body p { font-size: 15.4px; line-height: 18.6px; text-align: justify; margin-bottom: 26px; }

  .closing { position: absolute; left: 58px; top: 676px; font-size: 18px; font-weight: 500; }
  .signature { position: absolute; left: 50px; top: 734px; width: 168px; height: 56px; background: var(--signature-tone); }
  .signer-name { position: absolute; left: 52px; top: 818px; font-size: 18px; font-weight: 500; }
  .signer-role { position: absolute; left: 52px; top: 852px; font-size: 18px; font-weight: 500; }

  .contact-list { position: absolute; right: 53px; top: 826px; list-style: none; }
  .contact-item { display: flex; align-items: center; justify-content: flex-end; gap: 10px; font-size: 10.5px; font-weight: 500; line-height: 13px; text-align: right; }
  .contact-item + .contact-item { margin-top: 19px; }
  .contact-icon { width: 32px; height: 32px; border-radius: 50%; background: var(--brand-green); display: flex; align-items: center; justify-content: center; flex-shrink: 0; }
  .contact-icon svg { width: 18px; height: 18px; }
</style>
</head>
<body>
<main class="letterhead">
  <svg class="bands" viewBox="0 0 792 1120" width="792" height="1120" aria-hidden="true">
    <polygon class="band-green" points="0,0 405,0 359,50 0,50"/>
    <polygon class="band-dark" points="418,0 792,0 792,39 387,39"/>
    <polygon class="band-dark" points="0,1079 405,1079 372,1120 0,1120"/>
    <polygon class="band-green" points="424,1070 792,1070 792,1120 385,1120"/>
  </svg>

  <header class="brand">
    <div class="brand-mark"></div>
    <div>
      <div class="brand-name">NORVALE</div>
      <div class="brand-tagline">AIR CONDITIONING &amp; REFRIGERATION</div>
    </div>
  </header>

  <div class="recipient-name">Your&nbsp; Name Here</div>
  <div class="letter-date">Date : 4.6.2021</div>
  <div class="recipient-address">Address</div>

  <section class="letter-body">
    <p>Lorem ipsum dolor sit amet, consectetur adipiscing elit. Nam pretium quam eget feugiat tincidunt. Nullam consequat mi vitae pharetra sagittis. Suspendisse porta placerat velit, ac condimentum felis molestie in. Nullam eget velit in erat consectetur semper vitae ac nisi. Donec et lectus ut purus aliquam pulvinar non in arcu. Vestibulum et turpis a nisl placerat euismod. Aliquam eu quam augue. Cras consectetur, velit ut semper aliquam, odio tortor suscipit nulla, et vulputate dui risus at ante. Maecenas ac dignissim ex. Pellentesque in dignissim massa. Fusce at posuere lorem. Vivamus molestie nisl ac nisi rhoncus vulputate. Aenean augue arcu, maximus ut consequat in, lobortis sit amet lectus. Suspendisse dapibus auctor quam, sed tempor orci euismod accumsan. In hac habitasse platea dictumst. Suspendisse ut enim metus.</p>
    <p>Nullam at mi eros. Lorem ipsum dolor sit amet, consectetur adipiscing elit. Vestibulum tempus, sem id pharetra ultrices, magna nulla aliquet sapien, ac fringilla odio tortor in eros. Duis a urna sem. Nunc ac purus mattis, pharetra urna quis, ultrices quam. Proin ac sollicitudin dolor, ac feugiat turpis. Sed aliquet ornare nisi, vitae finibus tortor vehicula auctor.</p>
  </section>

  <div class="closing">Regards</div>
  <div class="signature" role="img" aria-label="Handwritten signature"></div>
  <div class="signer-name">Your Name Here</div>
  <div class="signer-role">Designation Here</div>

  <ul class="contact-list">
    <li class="contact-item">
      <span>+12345689<br>+12345689</span>
      <span class="contact-icon">
        <svg viewBox="0 0 24 24"><path fill="#fff" d="M6.6 10.8a15.1 15.1 0 0 0 6.6 6.6l2.2-2.2a1 1 0 0 1 1-.25 11.4 11.4 0 0 0 3.6.57 1 1 0 0 1 1 1V20a1 1 0 0 1-1 1A17 17 0 0 1 3 4a1 1 0 0 1 1-1h3.5a1 1 0 0 1 1 1c0 1.25.2 2.45.57 3.57a1 1 0 0 1-.25 1z"/></svg>
      </span>
    </li>
    <li class="contact-item">
      <span>www.yourwebsite.com</span>
      <span class="contact-icon">
        <svg viewBox="0 0 24 24" fill="none" stroke="#fff" stroke-width="1.6"><circle cx="12" cy="12" r="9"/><ellipse cx="12" cy="12" rx="4" ry="9"/><path d="M3 12h18M4.5 7.5h15M4.5 16.5h15"/></svg>
      </span>
    </li>
    <li class="contact-item">
      <span>yourgmail@.com</span>
      <span class="contact-icon">
        <svg viewBox="0 0 24 24" fill="none" stroke="#fff" stroke-width="1.6"><rect x="3" y="6" width="18" height="12"/><path d="M3 6l9 7 9-7M3 18l7-6M21 18l-7-6"/></svg>
      </span>
    </li>
  </ul>
</main>
</body>
</html>
```